Moxy Fen needs some awesome stationary

Do you have what it takes to get my brand? You either do or you don't, have a crack at a design and you my just win my business.

I don't want to waste your or my time, so put your creative genius on either a business card or envelope.

I however need a package of stationary that follows the same brand. I will message you to complete the remaining should I like your first submission.

Here is what I need, have a go!

Basically I need the following for my small business based in melbourne.
- Letterhead (printer ready and MS Word)
- Business Card
- Compliments Slip
- Envelope
- Proposal Cover Page (MS Word only)
- Presentation Folder
- Marbled Fox Cards
- Student Name Tent
- Index Cards
- Vell-Ka

I am establishing the brand and it must be modern, professional but also relaxed; that is not formal and not corporate. It represents a company are leaders, but small enough to care and operate like a bunch of friends. We are bringing people and conversations back to business, and turfing out all the bureaucracy and crazy and wasteful procedures. Its about "lets talk and figure it out together and find even better ways".

Target Market(s)

Mainly companies that build software products, but Agile practices are used in many other industries (even graphic design projects)

Industry/Entity Type

Information Technology

Font styles to use
Sans Serif

Colors
3176b5
aaaaaa

Requirements
Must have
• I like curves and circles and not boxes or rectangles.
• I want a colour rich design with my brand colours, but it must be balanced.
• I want more modern than traditional, but simple modern
Should not have
• Not corporate
• Please don't waste my time if your not going to think about it.
• Don't mess with my primary logo
• Don't change my colours
• Don't overlay logo on image

```html
<!DOCTYPE html>
<html lang="en">
<head>
<meta charset="utf-8">
<title>Moxy Fen – Presentation Folder</title>
<link href="https://fonts.googleapis.com/css2?family=Open+Sans:wght@400;600;700&display=swap" rel="stylesheet">
<style>
  :root {
    --backdrop: #8a8a8c;
    --brand-blue: #2c5aa0;
    --brand-grey: #939cab;
    --paper: #ffffff;
    --paper-tint: #f1f4f8;
    --ink-light: #ffffff;
  }
  html, body {
    margin: 0;
    padding: 0;
    width: 1200px;
    height: 875px;
    overflow: hidden;
    background: var(--backdrop);
  }
  .folder {
    display: block;
    width: 1200px;
    height: 875px;
    font-family: "Open Sans", Arial, sans-serif;
  }
  .flap { fill: var(--brand-grey); }
  .panel-blue { fill: var(--brand-blue); }
  .cover-white { fill: var(--paper); }
  .cover-tint { fill: var(--paper-tint); }
  .swoosh { fill: var(--brand-grey); }
  .brand-mark { fill: var(--brand-blue); }
  .brand-name {
    fill: var(--brand-blue);
    font-weight: 700;
    font-size: 38px;
  }
  .cover-phone {
    fill: var(--ink-light);
    font-weight: 700;
    font-size: 28px;
  }
  .cover-web {
    fill: var(--ink-light);
    font-size: 13px;
    letter-spacing: 1.6px;
  }
  .flap-web {
    fill: var(--ink-light);
    font-size: 9px;
    letter-spacing: 2.4px;
  }
  .back-details {
    fill: var(--ink-light);
    font-size: 9.5px;
  }
  .icon { fill: var(--ink-light); }
</style>
</head>
<body>
<svg class="folder" viewBox="0 0 1200 875" xmlns="http://www.w3.org/2000/svg" role="img" aria-label="Moxy Fen presentation folder, open and flat">
  <defs>
    <clipPath id="cover-window">
      <path d="M556,206 H986 V533 Q900,640 774,638 Q640,630 556,538 Z"/>
    </clipPath>
  </defs>

  <!-- Die-cut flaps -->
  <path class="flap top-flap" d="M574,206 L574,123 Q720,72 877,38 L902,71 C915,58 947,62 956,86 C965,110 960,136 947,141 L986,196 L986,206 Z"/>
  <path class="flap side-flap" d="M986,206 L1128,257 L1062,566 Q1046,630 992,636 L986,636 Z"/>
  <text class="flap-web" transform="translate(1040,465) rotate(-90)">www.moxy-fen.com.au</text>

  <!-- Back panel -->
  <rect class="panel-blue back-panel" x="134" y="206" width="422" height="579"/>
  <g class="back-details">
    <text x="161" y="681">PO Box 4418</text>
    <text x="161" y="694">Ashdale North</text>
    <text x="161" y="706">VIC 3199, Australia</text>
    <text x="162" y="720">Moxy Fen Pty Ltd</text>
    <text x="162" y="733">ABN 12 345 678 901</text>
    <text x="176" y="748">13 000 MOXY</text>
    <text x="176" y="761">www.moxy-fen.com.au</text>
  </g>
  <path class="icon phone-icon" d="M163,740 q1.5,-1 2.5,0.5 l1,1.6 q0.4,0.9 -0.5,1.5 q0.8,1.8 2.4,2.6 q0.6,-0.9 1.5,-0.5 l1.6,1 q1.4,1 0.3,2.4 q-1.6,1.4 -4.6,-0.6 q-3.2,-2.4 -4.6,-5.6 q-0.8,-2 0.4,-2.9 Z"/>
  <circle class="icon globe-icon" cx="166.5" cy="757.5" r="4.2"/>

  <!-- Front cover -->
  <rect class="panel-blue front-panel" x="556" y="206" width="430" height="579"/>
  <path class="cover-white" d="M556,206 H986 V533 Q900,640 774,638 Q640,630 556,538 Z"/>
  <g clip-path="url(#cover-window)">
    <circle class="cover-tint" cx="760" cy="560" r="360"/>
    <circle class="cover-white" cx="720" cy="520" r="150" opacity="0.6"/>
    <path class="cover-white" d="M986,250 C940,470 880,600 720,632 L986,640 Z" opacity="0.9"/>
    <path class="swoosh" d="M990,292 C955,468 890,596 720,630 C870,618 950,560 990,505 Z"/>
  </g>

  <!-- Brand name -->
  <circle class="brand-mark" cx="768" cy="370" r="44"/>
  <text class="brand-name" x="768" y="475" text-anchor="middle">Moxy Fen</text>

  <text class="cover-phone" x="768" y="719" text-anchor="middle">13 000 MOXY</text>
  <text class="cover-web" x="768" y="740" text-anchor="middle">www.moxy-fen.com.au</text>
</svg>
</body>
</html>
```